Business Card Design Project

I require a business card with the following information on them for various different people;
name
m:
f:
e:
I have a logo already and will attached that. We are in the construction industry. I require something clean and simple but eye catching at the same time. You can use another colour with our logo if you like and you can style the logo as well if you wish. I am open.
Also it needs to be front and back design.
Industry/Entity Type
Construction
Requirements
Must have
- Logo, name, mobile, fax and email address.
Front and back design

```html
<!DOCTYPE html>
<html lang="en">
<head>
<meta charset="utf-8">
<title>Northgate Developments – Business Card</title>
<link rel="stylesheet" href="https://fonts.googleapis.com/css2?family=Open+Sans:wght@400;600&display=swap">
<style>
  :root {
    --bg: #e4e4e2;
    --card-dark: #1c1a1a;
    --card-light: #ffffff;
    --card-light-shade: #ececec;
    --green: #4dba2f;
    --green-dark: #2f8f1c;
    --ink: #1e1e1e;
    --ink-soft: #3a3a3a;
    --white: #ffffff;
  }
  * { margin: 0; padding: 0; box-sizing: border-box; }
  html, body {
    width: 1200px; height: 944px; overflow: hidden;
    background: var(--bg);
    font-family: "Open Sans", Arial, sans-serif;
  }
  .canvas { position: relative; width: 1200px; height: 944px; }

  .card {
    position: absolute;
    width: 600px; height: 340px;
    border-radius: 26px;
    overflow: hidden;
  }

  /* Brand lock-up */
  .brand { display: flex; align-items: center; gap: 14px; white-space: nowrap; }
  .brand__mark { width: 34px; height: 34px; background: var(--green); flex: none; }
  .brand__name {
    color: var(--green);
    font-size: 34px; font-weight: 400; line-height: 1;
    letter-spacing: 0.3px;
  }

  /* Front: dark card */
  .card--front {
    left: 90px; top: 100px;
    background: var(--card-dark);
  }
  .card--front .brand { position: absolute; left: 66px; top: 130px; }
  .card--front .website {
    position: absolute; left: 0; right: 0; top: 228px;
    text-align: center;
    color: var(--white);
    font-size: 17px; letter-spacing: 2px;
  }

  /* Back: light card */
  .card--back {
    left: 510px; top: 500px;
    background: linear-gradient(180deg, var(--card-light) 0%, var(--card-light) 60%, var(--card-light-shade) 100%);
  }
  .card--back .brand { position: absolute; left: 58px; top: 66px; }
  .person { position: absolute; left: 58px; top: 150px; }
  .person__name { font-size: 22px; font-weight: 600; color: var(--ink); }
  .person__role { font-size: 14px; color: var(--green-dark); margin-top: 2px; }

  .contact { position: absolute; font-size: 15px; color: var(--ink-soft); }
  .contact li { list-style: none; display: flex; align-items: center; gap: 10px; height: 22px; white-space: nowrap; }
  .contact svg { width: 14px; height: 14px; flex: none; }
  .contact--phones { left: 64px; top: 236px; }
  .contact--online { left: 350px; top: 250px; }

  .band { position: absolute; left: 0; bottom: 0; width: 600px; height: 30px; }
</style>
</head>
<body>
<main class="canvas">

  <section class="card card--front" aria-label="Card front">
    <div class="brand">
      <span class="brand__mark"></span>
      <span class="brand__name">Northgate Developments</span>
    </div>
    <p class="website">www.northgatedev.com</p>
  </section>

  <section class="card card--back" aria-label="Card back">
    <div class="brand">
      <span class="brand__mark"></span>
      <span class="brand__name">Northgate Developments</span>
    </div>

    <div class="person">
      <p class="person__name">Mark Ellison</p>
      <p class="person__role">director</p>
    </div>

    <ul class="contact contact--phones">
      <li>
        <svg viewBox="0 0 14 14" aria-hidden="true"><path d="M3 1h2l1 3-1.5 1a7 7 0 0 0 4.5 4.5L10 8l3 1v2a2 2 0 0 1-2 2A10 10 0 0 1 1 3a2 2 0 0 1 2-2z" fill="var(--green)"/></svg>
        512-555-0140
      </li>
      <li>
        <svg viewBox="0 0 14 14" aria-hidden="true"><rect x="1" y="5" width="12" height="8" rx="1" fill="var(--green)"/><rect x="3" y="1" width="8" height="5" fill="var(--green-dark)"/></svg>
        512-555-0141
      </li>
    </ul>

    <ul class="contact contact--online">
      <li>
        <svg viewBox="0 0 14 14" aria-hidden="true"><rect x="1" y="3" width="12" height="9" rx="1" fill="var(--green)"/><path d="M1 3l6 5 6-5" stroke="#fff" stroke-width="1.2" fill="none"/></svg>
        info@northgatedev.com
      </li>
      <li>
        <svg viewBox="0 0 14 14" aria-hidden="true"><circle cx="7" cy="7" r="6" fill="var(--green)"/></svg>
        www.northgatedev.com
      </li>
    </ul>

    <svg class="band" viewBox="0 0 600 30" preserveAspectRatio="none" aria-hidden="true">
      <polygon points="0,6 460,6 448,30 0,30" fill="var(--green)"/>
      <polygon points="468,0 600,0 600,30 452,30" fill="var(--card-dark)"/>
    </svg>
  </section>

</main>
</body>
</html>
```